Building company buisness cards

We are looking for a sharp modern new look for our business cards.
We are a New Zealand based company that specialises in house and land packages.
We have attached a photo of the current logo and would like to see if it can be improved somehow if needed.
We are open to any colours but we have chosen green at this stage.
Feel free to change the font and make the logo smarter looking.
Play with the colours and see what looks best.

We want a card that looks so good know one will want to throw it away!

Target Market(s)

Home buyers

Industry/Entity Type

Building

Contact Information for Business Card

Derek Tolvane
0217394062
dtolvane@quillmarkhomesteads.co.nz
quillmarkhomesteads.co.nz

Font styles to use
Serif
Sans Serif

Colors

Designer to choose colors to be used in the design.

Requirements
Must have
• Logo and company name on one side, details on the other side
Nice to have
• Color codes for the original green are HEX #4a8028, RGB(74,128,40), CMYK(42,0,69,50)
• Round corners, Raised and/or spot UV

```html
<!DOCTYPE html>
<html lang="en">
<head>
<meta charset="utf-8">
<title>Quillmark Homesteads – Business Cards</title>
<link rel="stylesheet" href="https://fonts.googleapis.com/css2?family=Open+Sans:wght@400;600&display=swap">
<style>
  :root {
    --brand-green: #4a8028;
    --stripe-dark: #2a2a2a;
    --card-white: #ffffff;
    --text-grey: #3c3c3c;
    --backdrop: #e7e5e2;
  }
  * { box-sizing: border-box; margin: 0; padding: 0; }
  html, body {
    width: 1200px; height: 997px; overflow: hidden;
    background: var(--backdrop);
    font-family: "Open Sans", Arial, sans-serif;
  }
  .stage { position: relative; width: 1200px; height: 997px; }
  .card {
    position: absolute;
    width: 560px; height: 320px;
    background: var(--card-white);
    border-radius: 10px;
    overflow: hidden;
    box-shadow: 0 6px 18px rgba(0,0,0,0.12);
  }
  .card--front { left: 110px; top: 140px; }
  .card--back  { left: 530px; top: 510px; }

  .front-wave { position: absolute; inset: 0; width: 100%; height: 100%; }
  .holder { position: absolute; left: 34px; top: 30px; color: var(--card-white); }
  .holder__name { font-size: 20px; font-weight: 600; }
  .holder__title { font-size: 13px; font-weight: 400; margin-top: 2px; padding-left: 12px; }

  .company-name {
    display: flex; align-items: center; gap: 10px;
    color: var(--brand-green);
    font-weight: 600;
    white-space: nowrap;
  }
  .company-name__square {
    flex: none; background: var(--brand-green);
  }
  .card--front .company-name { position: absolute; right: 34px; top: 116px; font-size: 21px; }
  .card--front .company-name__square { width: 14px; height: 14px; }
  .card--back .company-name {
    position: absolute; left: 0; right: 0; top: 126px;
    justify-content: center; font-size: 32px;
  }
  .card--back .company-name__square { width: 22px; height: 22px; }

  .contacts { position: absolute; left: 34px; bottom: 34px; list-style: none; }
  .contacts li {
    display: flex; align-items: center; gap: 8px;
    font-size: 13px; color: var(--text-grey); line-height: 20px;
  }
  .contacts svg { width: 12px; height: 12px; flex: none; }

  .web-line {
    position: absolute; left: 0; right: 0; bottom: 44px;
    display: flex; align-items: center; justify-content: center; gap: 12px;
    font-size: 13px; color: var(--brand-green);
  }
  .web-line::before, .web-line::after {
    content: ""; width: 70px; height: 1px; background: var(--brand-green);
  }
</style>
</head>
<body>
<main class="stage">

  <section class="card card--front" aria-label="Card front with contact details">
    <svg class="front-wave" viewBox="0 0 560 320" preserveAspectRatio="none" aria-hidden="true">
      <path d="M0 0 H560 V18 C430 18 370 45 290 95 C210 145 100 150 0 160 Z" fill="var(--brand-green)"/>
      <path d="M0 170 C100 160 210 150 290 100 C370 50 430 26 560 24 V18 C430 20 370 44 290 94 C210 144 100 152 0 162 Z" fill="var(--card-white)"/>
      <path d="M0 182 C110 170 220 155 300 104 C380 54 440 32 560 28 V24 C440 28 372 52 292 102 C212 152 102 166 0 174 Z" fill="var(--stripe-dark)"/>
    </svg>
    <div class="holder">
      <p class="holder__name">Derek Tolvane</p>
      <p class="holder__title">President</p>
    </div>
    <p class="company-name"><span class="company-name__square"></span>Quillmark Homesteads</p>
    <ul class="contacts">
      <li>
        <svg viewBox="0 0 12 12"><path d="M2.5 1 L4.5 1 L5 3.5 L3.8 4.5 C4.5 6 6 7.5 7.5 8.2 L8.5 7 L11 7.5 L11 9.5 C11 10.3 10.3 11 9.5 11 C5 11 1 7 1 2.5 C1 1.7 1.7 1 2.5 1 Z" fill="var(--brand-green)"/></svg>
        0217394062
      </li>
      <li>
        <svg viewBox="0 0 12 12"><rect x="1" y="2.5" width="10" height="7" rx="1" fill="var(--brand-green)"/><path d="M1.5 3 L6 6.5 L10.5 3" stroke="#fff" stroke-width="1" fill="none"/></svg>
        dtolvane@quillmarkhomesteads.co.nz
      </li>
      <li>
        <svg viewBox="0 0 12 12"><circle cx="6" cy="6" r="5" fill="var(--brand-green)"/><path d="M1 6 H11 M6 1 C3.5 3.5 3.5 8.5 6 11 M6 1 C8.5 3.5 8.5 8.5 6 11" stroke="#fff" stroke-width="0.8" fill="none"/></svg>
        www.quillmarkhomesteads.co.nz
      </li>
    </ul>
  </section>

  <section class="card card--back" aria-label="Card back with company name">
    <p class="company-name"><span class="company-name__square"></span>Quillmark Homesteads</p>
    <p class="web-line">www.quillmarkhomesteads.co.nz</p>
  </section>

</main>
</body>
</html>
```